Stationery Design Project

I am looking to create stationary for our new airport valet company. I am looking for something modern and stylish.

i also want to have a faint picture of something in the background (like a hollogram) something related to valet.

Our company is called Harborline Valet & Concierge.
Updates

Project Deadline Extended
Reason: To Finalize the edits with the designer who has so far provided the total package of what we are looking for in stationary.

Target Market(s)

high end customers

Industry/Entity Type

Airport

Requirements
Must have
• 1. name of company
2. address
3. phone number (to be provided)
4. Harborline should be Black and Valet and Concierge should white
5. picture of valet or something relating to valet as a watermark on letterhead.

```html
<!DOCTYPE html>
<html lang="en">
<head>
<meta charset="utf-8">
<title>Harborline Valet &amp; Concierge – Business Card</title>
<link rel="stylesheet" href="https://fonts.googleapis.com/css2?family=Mulish:wght@400;700;800&display=swap">
<style>
  :root {
    --page-bg: #e7e8ea;
    --navy: #0e1034;
    --paper: #f7f8fa;
    --accent-ice: #a9d3db;
    --ink: #1b1d3a;
    --white: #ffffff;
    --photo-light: #b8c9e2;
    --photo-mid: #4a6ea8;
    --photo-deep: #1d2f6b;
  }
  * { box-sizing: border-box; margin: 0; padding: 0; }
  html, body {
    width: 1200px; height: 934px; overflow: hidden;
    background: var(--page-bg);
    font-family: "Mulish", "Century Gothic", sans-serif;
  }
  .sheet { position: relative; width: 1200px; height: 934px; }
  .card {
    position: absolute; left: 250px; width: 700px; height: 400px;
    overflow: hidden;
    box-shadow: 0 6px 18px rgba(0,0,0,0.12);
  }
  .card--back { top: 47px; background: var(--navy); }
  .card--front { top: 487px; background: var(--paper); }

  .card__photo {
    position: absolute; left: 0; top: 0;
    background: linear-gradient(125deg, var(--photo-light) 0%, var(--photo-mid) 45%, var(--photo-deep) 100%);
  }
  .card--back .card__photo { width: 410px; height: 215px; }
  .card--front .card__photo { width: 380px; height: 240px; }

  .accent-bar { position: absolute; background: var(--accent-ice); }
  .card--back .accent-bar { left: 26px; top: 262px; width: 22px; height: 90px; }
  .card--front .accent-bar { left: 22px; top: 310px; width: 22px; height: 90px; }

  .wordmark {
    position: absolute;
    font-weight: 400;
    text-transform: uppercase;
    line-height: 1.05;
  }
  .wordmark__name { display: block; font-size: 44px; letter-spacing: 2px; }
  .wordmark__tag { display: block; font-size: 19px; letter-spacing: 2.5px; margin-top: 6px; }
  .card--back .wordmark { left: 72px; top: 250px; color: var(--white); }
  .card--front .wordmark { left: 72px; top: 262px; color: var(--navy); }
  .card--front .wordmark__tag {
    display: inline-block;
    margin-top: 6px;
    padding: 6px 30px 6px 10px;
    background: var(--navy);
    color: var(--white);
  }

  .contact {
    position: absolute; left: 438px; top: 128px;
    color: var(--ink);
  }
  .contact__name { font-size: 18px; font-weight: 800; letter-spacing: 0.5px; text-transform: uppercase; }
  .contact__role { font-size: 14px; margin-top: 6px; }
  .contact__address { font-size: 14px; line-height: 1.45; margin-top: 40px; font-style: normal; }
  .contact__label { font-weight: 800; }
</style>
</head>
<body>
<main class="sheet">

  <section class="card card--back" aria-label="Card back">
    <div class="card__photo" role="img" aria-label="Photo of a valet handing car keys to a driver at a car door"></div>
    <div class="accent-bar"></div>
    <p class="wordmark">
      <span class="wordmark__name">Harborline</span>
      <span class="wordmark__tag">Valet &amp; Concierge</span>
    </p>
  </section>

  <section class="card card--front" aria-label="Card front">
    <div class="card__photo" role="img" aria-label="Photo of a valet handing car keys to a driver at a car door"></div>
    <div class="accent-bar"></div>
    <p class="wordmark">
      <span class="wordmark__name">Harborline</span>
      <span class="wordmark__tag">Valet &amp; Concierge</span>
    </p>
    <div class="contact">
      <p class="contact__name">Marcus Hale</p>
      <p class="contact__role">Manager</p>
      <address class="contact__address">
        1480 Tidewater Lane<br>
        Richmond, British<br>
        Columbia, V6X 2K9<br>
        <span class="contact__label">Tel:</span> 604.555.0182
      </address>
    </div>
  </section>

</main>
</body>
</html>
```